Business Card for Industrial Distributor

We need a business card design for an industrial distributor. We sell machine parts for the manufacturing and oil industry. We would like the cards to look clean and modern but with a touch of industry.

Our colors are blue/white.

Please feel free to visit our website www.korvelpartsco.com

Target Market(s)

mexican manufacturers in the automobile/aerospace industry

Industry/Entity Type

Industrial

Colors
ffffff
0555a3

```html
<!DOCTYPE html>
<html lang="en">
<head>
<meta charset="utf-8">
<title>Korvel Business Card</title>
<link href="https://fonts.googleapis.com/css2?family=Mulish:wght@400;700;800&display=swap" rel="stylesheet">
<style>
  :root {
    --blue: #0555a3;
    --navy: #2b2f8f;
    --deep: #23277a;
    --paper: #f3f1e8;
    --ink: #3a3a44;
    --white: #ffffff;
    --stage: #e6e8ee;
  }
  * { box-sizing: border-box; margin: 0; padding: 0; }
  html, body { width: 1200px; height: 786px; overflow: hidden; }
  body {
    background: var(--stage);
    font-family: "Mulish", sans-serif;
    display: flex; align-items: center; justify-content: center; gap: 60px;
  }
  .card {
    position: relative; width: 520px; height: 300px;
    border-radius: 18px; overflow: hidden;
    box-shadow: 0 10px 30px rgba(20, 25, 70, .18);
  }
  /* front */
  .card-front { background: var(--paper); color: var(--ink); }
  .card-front .swoosh { position: absolute; inset: 0; }
  .brand {
    position: absolute; display: flex; align-items: center; gap: 10px;
    font-weight: 800; letter-spacing: .5px; line-height: 1;
  }
  .card-front .brand { left: 40px; top: 56px; font-size: 44px; color: var(--navy); }
  .brand-dot { width: 36px; height: 36px; border-radius: 50%; background: currentColor; flex: none; }
  .contact { position: absolute; left: 292px; top: 110px; font-size: 12.5px; line-height: 1.35; }
  .contact .name { font-weight: 800; color: var(--navy); font-size: 14px; text-transform: uppercase; letter-spacing: .5px; }
  .contact .role { margin-bottom: 7px; }
  .contact ul { list-style: none; }
  .contact li { display: flex; align-items: center; gap: 7px; }
  .contact li svg { width: 13px; height: 13px; flex: none; }
  .contact .address { margin-top: 7px; }
  /* back */
  .card-back {
    background: radial-gradient(ellipse 70% 75% at 50% 45%, #3a7fd0 0%, var(--blue) 40%, var(--navy) 80%, var(--deep) 100%);
    color: var(--white);
  }
  .card-back .arcs { position: absolute; inset: 0; }
  .card-back .brand { left: 50%; top: 118px; transform: translateX(-50%); font-size: 56px; }
  .card-back .brand-dot { width: 46px; height: 46px; }
  .card-back .url { position: absolute; left: 0; right: 0; top: 186px; text-align: center; font-size: 14px; letter-spacing: .5px; }
</style>
</head>
<body>
  <section class="card card-front">
    <svg class="swoosh" viewBox="0 0 520 300" aria-hidden="true">
      <path d="M0 170 C90 210 200 250 340 300 L0 300 Z" fill="var(--blue)"/>
      <path d="M0 186 C90 228 190 262 300 300 L0 300 Z" fill="var(--navy)"/>
      <path d="M0 164 C90 204 205 246 350 300" fill="none" stroke="var(--paper)" stroke-width="4"/>
    </svg>
    <div class="brand"><span class="brand-dot"></span>Korvel</div>
    <div class="contact">
      <p class="name">Marco Elvany</p>
      <p class="role">General Manager</p>
      <ul>
        <li><svg viewBox="0 0 13 13"><rect width="13" height="13" rx="2" fill="var(--navy)"/><path d="M4 3 L5.5 3 L6 5 L5 6 Q6 8 7.5 8.5 L8.5 7.5 L10 8 L10 9.5 Q6 10 3.5 5 Z" fill="var(--white)"/></svg>(956) 555-0142</li>
        <li><svg viewBox="0 0 13 13"><rect width="13" height="13" rx="2" fill="var(--navy)"/><rect x="3" y="5" width="7" height="5" fill="var(--white)"/><rect x="4" y="2.5" width="5" height="3" fill="none" stroke="var(--white)"/></svg>(956) 555-0178</li>
        <li><svg viewBox="0 0 13 13"><rect width="13" height="13" rx="2" fill="var(--navy)"/><rect x="2.5" y="4" width="8" height="5.5" fill="none" stroke="var(--white)"/><path d="M2.5 4 L6.5 7 L10.5 4" fill="none" stroke="var(--white)"/></svg>sales@korvelpartsco.com</li>
        <li><svg viewBox="0 0 13 13"><rect width="13" height="13" rx="2" fill="var(--navy)"/><circle cx="6.5" cy="6.5" r="4" fill="none" stroke="var(--white)"/><path d="M2.5 6.5 H10.5 M6.5 2.5 V10.5" stroke="var(--white)"/></svg>www.korvelpartsco.com</li>
      </ul>
      <p class="address">4820 Harbor Mill Rd.<br>Laredo, TX 78045</p>
    </div>
  </section>

  <section class="card card-back">
    <svg class="arcs" viewBox="0 0 520 300" aria-hidden="true">
      <ellipse cx="260" cy="150" rx="210" ry="125" fill="none" stroke="var(--white)" stroke-opacity=".08" stroke-width="14"/>
      <ellipse cx="260" cy="150" rx="170" ry="95" fill="none" stroke="var(--white)" stroke-opacity=".06" stroke-width="8"/>
    </svg>
    <div class="brand"><span class="brand-dot"></span>Korvel</div>
    <p class="url">www.korvelpartsco.com</p>
  </section>
</body>
</html>
```